New website for a business that provides Tidewell Behaviour

A new website that details the services that are provided around Tidewell Behaviour for people with a disability through QPKV. There also needs to incorporate an about us and a staff page, Plus a referral form that is a google doc.
The business already has a web address that needs to be tailored.
Soft colours are preferred.
Do not have lots of pictures, keep them minimal.
A logo for the business is also needed to be incorporated, and this is a separate project that can be awarded to the website winner.
Website needs to be able to be used on WIX who will be the host for the design.

Target Market(s)

QPKV clients requiring behaviour support clician

Industry/Entity Type

Clinical behaviour support and analysis

Colors
00AB8E
00BBA5
67D7C9
C6EFE9
E9F9F6

Requirements
Must have
• Soft colours, preferable pale turquoise, minimal pictures, clean, sophisticated and classical look

```html
<!DOCTYPE html>
<html lang="en">
<head>
<meta charset="utf-8">
<title>Tidewell Behaviour</title>
<link rel="stylesheet" href="https://fonts.googleapis.com/css2?family=Montserrat:wght@600;700;800&family=Figtree:wght@400;500;600;700&display=swap">
<style>
:root{
  --teal:#00AB8E;
  --teal-2:#00BBA5;
  --teal-3:#67D7C9;
  --teal-4:#C6EFE9;
  --teal-5:#E9F9F6;
  --ink:#111111;
  --body:#555555;
  --grey-bg:#f4f4f4;
  --footer:#0b0b0b;
  --white:#ffffff;
}
*{box-sizing:border-box;margin:0;padding:0}
html,body{width:1200px;height:4310px;overflow:hidden}
body{font-family:"Figtree",sans-serif;color:var(--body);background:var(--white);position:relative}
.abs{position:absolute}
h1,h2,h3,.heading{font-family:"Montserrat",sans-serif;color:var(--ink);font-weight:800}
a{text-decoration:none;color:inherit}
.btn{display:inline-flex;align-items:center;justify-content:center;position:absolute;background:var(--teal);color:var(--white);font-family:"Montserrat",sans-serif;font-weight:700;font-size:14px;letter-spacing:.3px}
.btn::after{content:"";position:absolute;top:6px;right:6px;width:7px;height:7px;border-top:1.5px solid var(--white);border-right:1.5px solid var(--white)}
.eyebrow{font-family:"Montserrat",sans-serif;font-weight:700;font-size:14px;color:var(--teal);display:flex;align-items:center;gap:10px;text-transform:uppercase}
.eyebrow::before,.eyebrow::after{content:"";width:28px;height:2px;background:var(--teal)}
.eyebrow.left::after{display:none}
.center{left:0;width:1200px;justify-content:center;text-align:center}

/* hero */
.hero{position:absolute;left:0;top:0;width:1200px;height:708px;background:linear-gradient(100deg,#7d7368 0%,#9c8f82 35%,#b5a996 55%,#8d99b0 80%,#6d7d98 100%)}
.hero-shade{position:absolute;inset:0;background:linear-gradient(90deg,rgba(20,20,20,.55),rgba(20,20,20,.05) 60%)}
.nav{position:absolute;left:112px;top:25px;width:976px;height:74px;background:var(--white);display:flex;align-items:center}
.brand{font-family:"Montserrat",sans-serif;font-weight:800;font-size:23px;color:var(--ink);margin-left:33px;white-space:nowrap}
.nav-links{display:flex;gap:36px;margin-left:50px;font-size:15px;color:#222}
.nav-links .active{color:var(--teal)}
.hero h1{position:absolute;left:110px;top:255px;color:var(--white);font-size:52px;line-height:64px}
.hero-text{position:absolute;left:112px;top:396px;padding-left:10px;border-left:3px solid var(--teal);color:var(--white);font-weight:700;font-size:14px;line-height:26px;width:520px}
.btn-outline{position:absolute;left:266px;top:470px;width:172px;height:49px;border:1.5px solid var(--white);color:var(--white);font-family:"Montserrat",sans-serif;font-weight:700;font-size:14px;display:flex;align-items:center;justify-content:center}

/* about */
.photo{position:absolute}
.play{position:absolute;width:68px;height:68px;border-radius:50%;background:var(--teal);border:4px solid var(--white);display:flex;align-items:center;justify-content:center}
.about h2{position:absolute;left:572px;top:880px;font-size:34px;line-height:43px;width:520px}
.about p{position:absolute;left:574px;top:978px;width:530px;font-size:15px;line-height:26px}

/* services */
.services{position:absolute;left:0;top:1304px;width:1200px;height:631px;background:var(--grey-bg)}
.section-title{position:absolute;left:0;width:1200px;text-align:center;font-size:33px}
.card{position:absolute;top:233px;width:280px;height:318px;background:var(--white);border-radius:10px;box-shadow:0 12px 30px rgba(0,0,0,.07);text-align:center}
.card .icon{position:absolute;left:78px;top:-57px;width:124px;height:124px;border-radius:50%;background:var(--teal);display:flex;align-items:center;justify-content:center}
.card h3{position:absolute;top:103px;left:10px;right:10px;font-size:17px;line-height:28px;font-weight:700}
.card p{position:absolute;top:168px;left:18px;right:18px;font-size:15px;line-height:26px;color:#666}
.card .more{position:absolute;top:278px;left:0;right:0;font-family:"Montserrat",sans-serif;font-weight:700;font-size:14px;color:var(--teal)}

/* video */
.video-band{position:absolute;left:0;top:1935px;width:1200px;height:469px;background:linear-gradient(90deg,#1aa98f,#24b59c 50%,#1ba58e)}
.video-band .eyebrow{color:var(--white)}
.video-band .eyebrow::before,.video-band .eyebrow::after{background:var(--white)}
.video-frame{position:absolute;left:142px;top:2174px;width:918px;height:436px;background:var(--white);padding:6px;box-shadow:0 10px 30px rgba(0,0,0,.12)}
.video-frame .shot{width:100%;height:100%;background:linear-gradient(100deg,#6f8c5a,#9db07d 30%,#c2b7ad 55%,#7e9a6d 80%,#5d7a4e)}

/* team */
.member{position:absolute;top:2814px;width:288px;height:360px}
.member .plus{position:absolute;right:0;top:0;width:40px;height:40px;background:var(--white);color:var(--teal);font-size:24px;font-weight:700;display:flex;align-items:center;justify-content:center}
.member .name{position:absolute;left:18px;bottom:18px;font-family:"Montserrat",sans-serif;font-weight:800;font-size:19px;color:var(--white)}
.member .role{position:absolute;left:20px;bottom:18px;font-family:"Montserrat",sans-serif;font-weight:700;font-size:13px;color:var(--white)}

/* testimonials */
.testimonials{position:absolute;left:0;top:3276px;width:1200px;height:624px;background:var(--grey-bg)}
.avatar{position:absolute;border-radius:50%;border:3px solid var(--white)}
.quote{position:absolute;left:218px;top:290px;width:764px;text-align:center;font-size:15.5px;line-height:26px;color:#333}
.dots{position:absolute;top:511px;left:0;width:1200px;display:flex;justify-content:center;gap:4px}
.dots span{width:10px;height:10px;border-radius:50%;background:var(--teal)}
.dots span.off{background:var(--white);border:1.5px solid var(--teal)}

/* footer */
.footer{position:absolute;left:0;top:3900px;width:1200px;height:410px;background:var(--footer);color:var(--white)}
.footer .logo{position:absolute;left:112px;top:100px;width:262px;text-align:center;font-family:"Montserrat",sans-serif;font-weight:800;font-size:36px;line-height:44px;color:var(--white)}
.socials{position:absolute;left:200px;top:232px;display:flex;gap:14px}
.socials span{width:10px;height:10px;border-radius:50%;background:var(--teal)}
.col-title{position:absolute;top:90px;font-family:"Montserrat",sans-serif;font-weight:700;font-size:17px;color:var(--white)}
.col-links{position:absolute;top:128px;list-style:none;font-size:15px;line-height:30px;color:#e8e8e8}
.email{position:absolute;left:777px;top:123px;width:244px;height:32px;border-bottom:1px solid #444;border-left:2px solid var(--white);padding-left:12px;font-size:14px;color:#555;display:flex;align-items:center}
.subscribe{position:absolute;left:778px;top:186px;width:120px;height:37px;border-radius:20px;background:var(--teal);color:var(--white);font-family:"Montserrat",sans-serif;font-weight:700;font-size:12px;display:flex;align-items:center;justify-content:center;box-shadow:0 0 18px rgba(0,171,142,.7)}
.divider{position:absolute;left:112px;top:307px;width:976px;height:1px;background:#2a2a2a}
.copy{position:absolute;left:0;top:348px;width:1200px;text-align:center;font-size:15px;color:#eee}
</style>
</head>
<body>

<!-- Hero -->
<section class="hero">
  <div role="img" aria-label="Photo of a young man and a support worker clasping hands" style="position:absolute;inset:0"></div>
  <div class="hero-shade"></div>
  <nav class="nav">
    <span class="brand">TIDEWELL BEHAVIOUR</span>
    <div class="nav-links">
      <a class="active" href="#">Home</a><a href="#">Services</a><a href="#">Our Team</a><a href="#">About Us</a><a href="#">Contact Us</a>
    </div>
    <a class="btn" href="#" style="left:859px;top:13px;width:95px;height:47px">LOGIN</a>
  </nav>
  <h1>WELCOME TO<br>TIDEWELL BEHAVIOUR</h1>
  <p class="hero-text">Lorem ipsum dolor sit amet, consectetur adipiscing elit, sed do eiusmod tempor incididunt ut labore et dolore magna aliqua.</p>
  <a class="btn" href="#" style="left:112px;top:470px;width:137px;height:49px">GET STARTED</a>
  <a class="btn-outline" href="#">REFERRAL FORM</a>
</section>

<!-- About -->
<section class="about">
  <div class="photo" role="img" aria-label="Photo of a person in a wheelchair beside a vehicle ramp" style="left:112px;top:798px;width:303px;height:329px;background:linear-gradient(160deg,#b9c4cc,#6f7a80 55%,#3b3f42)"></div>
  <div class="play" style="left:381px;top:870px">
    <svg width="18" height="20" viewBox="0 0 18 20"><path d="M2 1 L17 10 L2 19Z" fill="#fff"/></svg>
  </div>
  <div class="photo" role="img" aria-label="Photo of a carer assisting a woman in a wheelchair at home" style="left:238px;top:1028px;width:298px;height:189px;background:linear-gradient(90deg,#dfe9ee,#c9d6dc 40%,#a9a48a 70%,#d8d2b4);border:4px solid #fff;border-width:4px 0 0 4px"></div>
  <div class="eyebrow left abs" style="left:573px;top:852px">About Us</div>
  <h2>WELCOME TO TIDEWELL BEHAVIOUR</h2>
  <p>Lorem ipsum dolor sit amet, consectetur adipiscing elit, sed do eiusmod tempor incididunt ut labore et dolore magna aliqua. Quis ipsum suspendisse ultrices gravida. Risus commodo viverra maecenas accumsan lacus vel facilisis. Lorem ipsum dolor sit amet, consectetur adipiscing elit, sed do eiusmod tempor incididunt ut labore et dolore magna aliqua. Quis ipsum</p>
  <a class="btn" href="#" style="left:574px;top:1135px;width:139px;height:47px">LEARN MORE</a>
</section>

<!-- Services -->
<section class="services">
  <div class="eyebrow abs center" style="top:71px">Services</div>
  <h2 class="section-title" style="top:98px">OUR SERVICES</h2>

  <article class="card" style="left:124px">
    <div class="icon"><svg width="58" height="58" viewBox="0 0 58 58" fill="none" stroke="#fff" stroke-width="2.2"><circle cx="22" cy="40" r="12"/><circle cx="22" cy="40" r="4"/><path d="M14 10v18h16l6 14h6M10 16h8"/><path d="M38 8l10 4v8c0 6-4 10-10 12-6-2-10-6-10-12v-8z"/><path d="M34 19l3 3 6-6"/></svg></div>
    <h3>DISABILITY EMPLOYMENT SERVICES (DES)</h3>
    <p>Lorem ipsum dolor sit amet, consectetur adipiscing elit, sed do eiusmod tempor incididunt ut labore et dolore magna aliqua.</p>
    <a class="more" href="#">LEARN MORE</a>
  </article>

  <article class="card" style="left:460px">
    <div class="icon"><svg width="58" height="58" viewBox="0 0 58 58" fill="none" stroke="#fff" stroke-width="2.2"><circle cx="29" cy="18" r="9"/><path d="M20 14h18M26 8h6"/><path d="M14 50c0-10 6-17 15-17s15 7 15 17z"/><path d="M26 40h6M29 37v6"/><circle cx="12" cy="38" r="4"/><circle cx="46" cy="38" r="4"/></svg></div>
    <h3>COMUUNITY NURSING CARE SERVICES (CNC)</h3>
    <p>Lorem ipsum dolor sit amet, consectetur adipiscing elit, sed do eiusmod tempor incididunt ut labore et dolore magna aliqua.</p>
    <a class="more" href="#">LEARN MORE</a>
  </article>

  <article class="card" style="left:797px">
    <div class="icon"><svg width="58" height="58" viewBox="0 0 58 58" fill="none" stroke="#fff" stroke-width="2.2"><path d="M14 18h30v12H14z"/><path d="M18 18v-6h22v6M20 30v8M38 30v8"/><path d="M10 50c4-8 10-12 19-12s15 4 19 12"/><path d="M8 24h6M44 24h6"/></svg></div>
    <h3>TRANSPORTATION ASSISTANCE SERVICES (TAS)</h3>
    <p>Lorem ipsum dolor sit amet, consectetur adipiscing elit, sed do eiusmod tempor incididunt ut labore et dolore magna aliqua.</p>
    <a class="more" href="#">LEARN MORE</a>
  </article>
</section>

<!-- Videos -->
<section class="video-band" role="img" aria-label="Teal-tinted background photo of a man in a wheelchair outdoors">
  <div class="eyebrow abs center" style="top:54px">Video</div>
  <h2 class="section-title" style="top:88px;color:#fff">OUR VIDEOS</h2>
  <p class="abs" style="left:270px;top:145px;width:660px;text-align:center;color:#fff;font-size:15px;line-height:26px">Lorem ipsum dolor sit amet, consectetur adipiscing elit, sed do eiusmod tempor incididunt ut labore et dolore magna aliqua. Quis ipsum suspendisse ultrices gravida.</p>
</section>
<div class="video-frame">
  <div class="shot" role="img" aria-label="Video still of a smiling boy in a wheelchair with a carer in a park"></div>
  <div class="play" style="left:400px;top:182px;width:74px;height:74px">
    <svg width="18" height="20" viewBox="0 0 18 20"><path d="M2 1 L17 10 L2 19Z" fill="#fff"/></svg>
  </div>
</div>

<!-- Team -->
<div class="eyebrow abs center" style="top:2700px">Team</div>
<h2 class="section-title" style="top:2733px">OUR STAFF</h2>

<div class="member" style="left:0;background:linear-gradient(180deg,#6b6e72,#4e5560 70%,#2f7f95)" role="img" aria-label="Portrait photo of a staff member">
  <span class="plus">+</span><span class="name">OWEN MARSH</span>
</div>
<div class="member" style="left:305px;background:linear-gradient(180deg,#2fb89f,#1fa98f)" role="img" aria-label="Portrait photo of a staff member with teal overlay">
  <span class="plus">+</span><span class="name" style="bottom:48px">ELLIS HARTLEY</span><span class="role">VICE PRESIDENT</span>
</div>
<div class="member" style="left:608px;background:linear-gradient(180deg,#6d655f,#8a6a58 60%,#9c3440)" role="img" aria-label="Portrait photo of a staff member">
  <span class="plus">+</span><span class="name">NORA QUILL</span>
</div>
<div class="member" style="left:912px;background:linear-gradient(180deg,#8a8580,#a58d79 55%,#e8e4de)" role="img" aria-label="Portrait photo of a staff member">
  <span class="plus">+</span><span class="name">MAYA CORRAN</span>
</div>

<!-- Testimonials -->
<section class="testimonials">
  <div class="eyebrow abs center" style="top:73px">Testimonials</div>
  <h2 class="section-title" style="top:108px">OUR CLIENTS</h2>
  <div class="avatar" role="img" aria-label="Client photo" style="left:525px;top:205px;width:44px;height:44px;background:#8a7a6d"></div>
  <div class="avatar" role="img" aria-label="Client photo" style="left:621px;top:205px;width:44px;height:44px;background:#a07a62"></div>
  <div class="avatar" role="img" aria-label="Client photo" style="left:565px;top:194px;width:64px;height:64px;background:#5e6a70;border-color:var(--teal)"></div>
  <svg class="abs" style="left:540px;top:262px" width="120" height="60" viewBox="0 0 120 60"><path d="M20 55 L45 5 H70 L45 55Z M60 55 L85 5 H110 L85 55Z" fill="#dfeeed"/></svg>
  <p class="quote">Lorem ipsum dolor sit amet, consectetur adipiscing elit, sed do eiusmod tempor incididunt ut labore et dolore magna aliqua. Quis ipsum suspendisse ultrices gravida. Risus commodo viverra maecenas accumsan lacus vel facilisis. Lorem ipsum dolor sit amet, consectetur adipiscing elit, sed do eiusmod tempor incididunt ut labore et dolore magna aliqua.</p>
  <div class="abs heading" style="left:0;top:427px;width:1200px;text-align:center;font-size:17px;font-weight:700">Harper Linden</div>
  <div class="abs" style="left:0;top:452px;width:1200px;text-align:center;font-size:13px;color:#333">Lorem Ipsum</div>
  <div class="dots"><span></span><span></span><span class="off"></span><span></span><span></span></div>
</section>

<!-- Footer -->
<footer class="footer">
  <div class="logo">TIDEWELL<br>BEHAVIOUR</div>
  <div class="socials" aria-label="Social links"><span></span><span></span><span></span><span></span></div>

  <div class="col-title" style="left:430px">QUICK LINKS</div>
  <ul class="col-links" style="left:432px"><li>Home</li><li>Services</li><li>Our Team</li><li>About Us</li><li>Contact Us</li></ul>

  <div class="col-title" style="left:599px">SUPPORT</div>
  <ul class="col-links" style="left:602px"><li>Terms&amp;condtions</li><li>Privacy Policy</li><li>About Us</li><li>Support</li></ul>

  <div class="col-title" style="left:777px">SUBSCRIBE TO OUR NEWSLETTER</div>
  <div class="email">Enter Your Email</div>
  <a class="subscribe" href="#">SUBSCRIBE</a>

  <div class="divider"></div>
  <div class="copy">©Copyrights 2024 &nbsp;Tidewell Behaviour &nbsp; | &nbsp; All Rights Reserved</div>
</footer>

</body>
</html>
```